Specialist aerospace company requires Powerpoint template

We are a company who delivers specialist engineering and testing services. We would like an updated Powerpoint template - specifically one that will be suitable to use in the production of training materials.
We would therefore like the following included:
-Our logo
-A copyright notice
-The course name (e.g. High Voltage Basics)
-The lesson name (e.g. Safe Clearances)
We wish to convey a professional image.

```html
<!DOCTYPE html>
<html lang="en">
<head>
<meta charset="utf-8">
<title>Stratavolt Aero – Training Presentation Template</title>
<link rel="stylesheet" href="https://fonts.googleapis.com/css2?family=Open+Sans:wght@400;600;700;800&display=swap">
<style>
  :root {
    --brand-blue: #3b6894;
    --brand-blue-dark: #24486e;
    --brand-blue-light: #5d88b3;
    --ink: #1e2733;
    --ink-soft: #4a5563;
    --ink-muted: #8a929c;
    --slide-bg: #f1f2f4;
    --page-bg: #ffffff;
    --white: #ffffff;
  }
  * { box-sizing: border-box; margin: 0; padding: 0; }
  html, body { width: 1200px; height: 4336px; overflow: hidden; }
  body { background: var(--page-bg); font-family: "Open Sans", Arial, sans-serif; color: var(--ink); position: relative; }

  .slide { position: absolute; left: 20px; width: 1160px; height: 656px; background: var(--slide-bg); overflow: hidden; }
  .slide--welcome { top: 0; height: 660px; }
  .slide--about { top: 732px; }
  .slide--course { top: 1460px; }
  .slide--lesson { top: 2188px; }
  .slide--engineering { top: 2912px; }
  .slide--thanks { top: 3620px; height: 680px; background: var(--white); }

  .photo { position: absolute; border-radius: 2px; }

  /* header band */
  .slide-header { position: absolute; left: 0; top: 28px; width: 1160px; height: 56px; }
  .slide-header svg { position: absolute; left: 0; top: 0; }
  .slide-header__title { position: absolute; left: 104px; top: 10px; color: var(--white); font-weight: 700; font-size: 28px; letter-spacing: .5px; white-space: nowrap; }
  .brand { position: absolute; display: flex; align-items: center; gap: 10px; font-weight: 700; color: var(--brand-blue-dark); white-space: nowrap; }
  .brand__mark { background: var(--brand-blue); display: block; }
  .slide-header .brand { right: 40px; top: 10px; font-size: 26px; }
  .slide-header .brand__mark { width: 26px; height: 26px; }

  .slide-footer { position: absolute; left: 0; bottom: 0; width: 100%; height: 44px; background: var(--brand-blue); }
  .slide-footer__stripes { position: absolute; left: 0; top: 0; }
  .copyright { position: absolute; right: 40px; top: 12px; color: var(--white); font-size: 14px; }

  /* welcome */
  .welcome__photo { left: 0; top: 0; width: 1160px; height: 660px; background: linear-gradient(180deg, #5c8ec4 0%, #2f639a 45%, #1f4a78 75%, #183a5e 100%); }
  .welcome__text { position: absolute; left: 0; width: 100%; text-align: center; color: var(--white); }
  .welcome__lead { top: 190px; font-size: 66px; font-weight: 400; }
  .welcome__brand { top: 268px; font-size: 104px; font-weight: 700; display: flex; justify-content: center; align-items: center; gap: 22px; }
  .welcome__brand span.sq { width: 70px; height: 70px; background: var(--white); display: inline-block; }
  .welcome__copy { position: absolute; left: 0; width: 100%; bottom: 30px; text-align: center; color: var(--white); font-size: 14px; }

  .heading { position: absolute; font-weight: 800; color: var(--ink); letter-spacing: .3px; }
  .body { position: absolute; font-size: 17px; line-height: 1.45; color: var(--ink-soft); }
  .body--muted { color: var(--ink-muted); }

  /* about */
  .about__photo { left: 52px; top: 110px; width: 488px; height: 440px; background: linear-gradient(135deg, #3a4e66, #7aa1c6 55%, #2c3d52); }
  .about .heading { left: 606px; top: 116px; font-size: 30px; }
  .bullet-list { position: absolute; left: 606px; top: 170px; width: 500px; list-style: none; }
  .bullet-list li { display: flex; gap: 14px; font-size: 17px; line-height: 1.45; color: var(--ink-soft); margin-bottom: 22px; }
  .bullet-list li:first-child { color: var(--ink); }
  .bullet-list svg { flex: none; margin-top: 4px; }

  /* course */
  .course .heading { left: 0; width: 100%; text-align: center; top: 122px; font-size: 32px; }
  .course__intro { left: 40px; width: 1080px; top: 178px; text-align: center; color: var(--ink); }
  .course__note { left: 40px; width: 1080px; top: 250px; text-align: center; font-size: 15px; }
  .photo-row { position: absolute; left: 28px; top: 336px; display: flex; gap: 24px; }
  .photo-row .photo { position: static; width: 254px; height: 220px; }

  /* lesson */
  .lesson .heading { left: 110px; top: 106px; font-size: 32px; }
  .lesson__intro { left: 110px; top: 158px; width: 500px; color: var(--ink); }
  .lesson__body { left: 110px; top: 290px; width: 500px; font-size: 15.5px; }
  .photo-grid { position: absolute; left: 628px; top: 104px; display: grid; grid-template-columns: 240px 240px; gap: 24px; }
  .photo-grid .photo { position: static; width: 240px; height: 210px; }

  /* engineering */
  .eng__bg { left: 0; top: 0; width: 1160px; height: 656px; background: linear-gradient(180deg, #dfe6ee 0%, #eef1f4 60%, #e3e8ee 100%); }
  .eng__diagram { position: absolute; left: 0; top: 0; }
  .feature-title { position: absolute; font-size: 14px; font-weight: 700; color: var(--ink); white-space: nowrap; }
  .feature-text { position: absolute; width: 250px; font-size: 11.5px; line-height: 1.45; color: var(--ink-soft); }

  /* thanks */
  .thanks__photo { left: 0; top: 0; width: 560px; height: 680px; background: linear-gradient(160deg, #8fa4b9 0%, #3c5676 45%, #1f3450 100%); }
  .thanks .brand { left: 620px; top: 70px; font-size: 54px; gap: 18px; }
  .thanks .brand__mark { width: 56px; height: 56px; }
  .thanks__title { position: absolute; left: 620px; top: 176px; font-size: 76px; line-height: 1.2; font-weight: 800; color: var(--brand-blue-dark); letter-spacing: 1px; white-space: nowrap; }
  .thanks__tagline { position: absolute; left: 620px; top: 298px; font-size: 22px; color: var(--ink-soft); white-space: nowrap; }
  .contact { position: absolute; left: 620px; display: flex; align-items: center; gap: 16px; font-size: 26px; font-weight: 600; color: var(--ink); white-space: nowrap; }
  .contact--email { top: 360px; }
  .contact--phone { top: 416px; }
  .socials { position: absolute; left: 640px; top: 486px; display: flex; gap: 20px; }
  .socials span { width: 46px; height: 46px; border-radius: 50%; border: 2px solid var(--ink-muted); display: block; }
  .thanks__copy { position: absolute; left: 620px; bottom: 36px; font-size: 15px; color: var(--ink-soft); }
</style>
</head>
<body>

<!-- Title slide -->
<section class="slide slide--welcome">
  <div class="photo welcome__photo" role="img" aria-label="Passenger jet flying above clouds and a coastline"></div>
  <p class="welcome__text welcome__lead">Welcome to</p>
  <p class="welcome__text welcome__brand"><span class="sq"></span>Stratavolt</p>
  <p class="welcome__copy">© Copyright 2023 Stratavolt Aero. All rights reserved.</p>
</section>

<!-- About -->
<section class="slide slide--about about">
  <header class="slide-header">
    <svg width="800" height="56" viewBox="0 0 800 56">
      <path d="M0 0 H690 L656 56 H0 Z" fill="var(--brand-blue)"/>
      <path d="M52 0 H70 L36 56 H18 Z M78 0 H88 L54 56 H44 Z" fill="var(--brand-blue-light)"/>
      <path d="M702 0 H716 L682 56 H668 Z M728 0 H742 L708 56 H694 Z M754 0 H768 L734 56 H720 Z" fill="var(--brand-blue)"/>
    </svg>
    <h2 class="slide-header__title">ABOUT US</h2>
    <div class="brand"><span class="brand__mark"></span>Stratavolt</div>
  </header>
  <div class="photo about__photo" role="img" aria-label="Two engineers studying a holographic aircraft model"></div>
  <h1 class="heading">STRATAVOLT AERO</h1>
  <ul class="bullet-list">
    <li><svg width="20" height="20" viewBox="0 0 20 20"><circle cx="10" cy="10" r="10" fill="var(--brand-blue)"/><path d="M5.5 10.5 L8.5 13.5 L14.5 7" stroke="#fff" stroke-width="2.2" fill="none"/></svg>
      <span>Sed ut perspiciatis unde omnis iste natus error sit voluptatem accusantium doloremque laudantium, totam rem aperiam, eaque ipsa quae ab illo inventore veritatis et quasi architecto beatae vitae dicta sunt explicabo. Nemo</span></li>
    <li><svg width="20" height="20" viewBox="0 0 20 20"><circle cx="10" cy="10" r="10" fill="var(--brand-blue)"/><path d="M5.5 10.5 L8.5 13.5 L14.5 7" stroke="#fff" stroke-width="2.2" fill="none"/></svg>
      <span>enim ipsam voluptatem quia voluptas sit aspernatur aut odit aut fugit, sed quia consequuntur magni dolores eos qui ratione voluptatem sequi nesciunt. Neque porro quisquam est, qui dolorem ipsum quia dolor sit amet, consectetur, adipisci velit, sed quia non numquam eius modi tempora incidunt ut labore et dolore magnam aliquam quaerat voluptatem.</span></li>
  </ul>
  <footer class="slide-footer">
    <svg class="slide-footer__stripes" width="140" height="44" viewBox="0 0 140 44"><path d="M40 0 H58 L30 44 H12 Z M66 0 H76 L48 44 H38 Z" fill="var(--brand-blue-light)"/></svg>
    <p class="copyright">© Copyright 2023 Stratavolt Aero. All rights reserved.</p>
  </footer>
</section>

<!-- Course -->
<section class="slide slide--course course">
  <header class="slide-header">
    <svg width="800" height="56" viewBox="0 0 800 56">
      <path d="M0 0 H690 L656 56 H0 Z" fill="var(--brand-blue)"/>
      <path d="M52 0 H70 L36 56 H18 Z M78 0 H88 L54 56 H44 Z" fill="var(--brand-blue-light)"/>
      <path d="M702 0 H716 L682 56 H668 Z M728 0 H742 L708 56 H694 Z M754 0 H768 L734 56 H720 Z" fill="var(--brand-blue)"/>
    </svg>
    <h2 class="slide-header__title">THE COURSE</h2>
    <div class="brand"><span class="brand__mark"></span>Stratavolt</div>
  </header>
  <h1 class="heading">HIGH VOLTAGE BASICS</h1>
  <p class="body course__intro">Sed ut perspiciatis unde omnis iste natus error sit voluptatem accusantium doloremque laudantium, totam rem aperiam, eaque ipsa quae ab illo inventore veritatis et quasi architecto beatae vitae dicta sunt explicabo. Nemo</p>
  <p class="body body--muted course__note">enim ipsam voluptatem quia voluptas sit aspernatur aut odit aut fugit, sed quia consequuntur magni dolores eos qui ratione voluptatem sequi nesciunt. Neque porro quisquam est, qui dolorem ipsum quia dolor sit amet, consectetur, adipisci velit, sed quia non numquam eius modi tempora incidunt ut labore et dolore magnam aliquam quaerat voluptatem.</p>
  <div class="photo-row">
    <div class="photo" role="img" aria-label="Close view of a jet engine fan" style="background:linear-gradient(135deg,#9fb0c2,#4d6076)"></div>
    <div class="photo" role="img" aria-label="Technicians working beside an aircraft" style="background:linear-gradient(135deg,#c7b79a,#5c6a78)"></div>
    <div class="photo" role="img" aria-label="Engineer inspecting engine components" style="background:linear-gradient(135deg,#7c8794,#3b4652)"></div>
    <div class="photo" role="img" aria-label="Aircraft parked in a maintenance hangar" style="background:linear-gradient(135deg,#d9dee4,#8494a6)"></div>
  </div>
  <footer class="slide-footer">
    <svg class="slide-footer__stripes" width="140" height="44" viewBox="0 0 140 44"><path d="M40 0 H58 L30 44 H12 Z M66 0 H76 L48 44 H38 Z" fill="var(--brand-blue-light)"/></svg>
    <p class="copyright">© Copyright 2023 Stratavolt Aero. All rights reserved.</p>
  </footer>
</section>

<!-- Lesson -->
<section class="slide slide--lesson lesson">
  <header class="slide-header">
    <svg width="800" height="56" viewBox="0 0 800 56">
      <path d="M0 0 H690 L656 56 H0 Z" fill="var(--brand-blue)"/>
      <path d="M52 0 H70 L36 56 H18 Z M78 0 H88 L54 56 H44 Z" fill="var(--brand-blue-light)"/>
      <path d="M702 0 H716 L682 56 H668 Z M728 0 H742 L708 56 H694 Z M754 0 H768 L734 56 H720 Z" fill="var(--brand-blue)"/>
    </svg>
    <h2 class="slide-header__title">THE LESSON</h2>
    <div class="brand"><span class="brand__mark"></span>Stratavolt</div>
  </header>
  <h1 class="heading">SAFE CLEARANCES</h1>
  <p class="body lesson__intro">Sed ut perspiciatis unde omnis iste natus error sit voluptatem accusantium doloremque laudantium, totam rem aperiam, eaque ipsa quae ab illo inventore veritatis et quasi architecto beatae vitae dicta sunt explicabo. Nemo</p>
  <p class="body lesson__body">enim ipsam voluptatem quia voluptas sit aspernatur aut odit aut fugit, sed quia consequuntur magni dolores eos qui ratione voluptatem sequi nesciunt. Neque porro quisquam est, qui dolorem ipsum quia dolor sit amet, consectetur, adipisci velit, sed quia non numquam eius modi tempora incidunt ut labore et dolore magnam aliquam quaerat voluptatem. enim ipsam voluptatem quia voluptas sit aspernatur aut odit aut fugit, sed quia consequuntur magni dolores eos qui ratione voluptatem sequi nesciunt. Neque porro quisquam est, qui dolorem.</p>
  <div class="photo-grid">
    <div class="photo" role="img" aria-label="Engineer working inside an engine nacelle" style="background:linear-gradient(135deg,#8996a4,#3e4a58)"></div>
    <div class="photo" role="img" aria-label="Technician repairing aircraft equipment" style="background:linear-gradient(135deg,#b8c4d0,#4f6f92)"></div>
    <div class="photo" role="img" aria-label="Mechanic servicing a large turbine" style="background:linear-gradient(135deg,#9ea7b0,#505a66)"></div>
    <div class="photo" role="img" aria-label="Team reviewing work on a laptop in a hangar" style="background:linear-gradient(135deg,#c9d3dd,#3f6a96)"></div>
  </div>
  <footer class="slide-footer">
    <svg class="slide-footer__stripes" width="140" height="44" viewBox="0 0 140 44"><path d="M40 0 H58 L30 44 H12 Z M66 0 H76 L48 44 H38 Z" fill="var(--brand-blue-light)"/></svg>
    <p class="copyright">© Copyright 2023 Stratavolt Aero. All rights reserved.</p>
  </footer>
</section>

<!-- Engineering -->
<section class="slide slide--engineering">
  <div class="photo eng__bg" role="img" aria-label="Faint aircraft on a runway under a pale sky"></div>
  <svg class="eng__diagram" width="1160" height="656" viewBox="0 0 1160 656">
    <g stroke="var(--brand-blue-dark)" stroke-width="2" fill="none">
      <path d="M168 136 H440 L510 230"/>
      <path d="M168 312 H440"/>
      <path d="M168 488 H440 L510 420"/>
      <path d="M992 136 H720 L650 230"/>
      <path d="M992 312 H720"/>
      <path d="M992 488 H720 L650 420"/>
      <circle cx="580" cy="325" r="142" stroke-width="3"/>
    </g>
    <circle cx="580" cy="325" r="118" fill="#e8edf2"/>
    <rect x="535" y="280" width="90" height="90" fill="var(--brand-blue)"/>
    <g fill="var(--brand-blue-dark)">
      <circle cx="440" cy="312" r="6"/><circle cx="720" cy="312" r="6"/>
      <circle cx="510" cy="230" r="6"/><circle cx="650" cy="230" r="6"/>
      <circle cx="510" cy="420" r="6"/><circle cx="650" cy="420" r="6"/>
    </g>
    <g fill="var(--brand-blue)" stroke="#fff" stroke-width="3">
      <circle cx="130" cy="136" r="34"/><circle cx="130" cy="312" r="34"/><circle cx="130" cy="488" r="34"/>
      <circle cx="1030" cy="136" r="34"/><circle cx="1030" cy="312" r="34"/><circle cx="1030" cy="488" r="34"/>
    </g>
    <g stroke="#fff" stroke-width="2.5" fill="none" stroke-linecap="round">
      <path d="M118 148 L142 124 M122 124 H142 V144"/>
      <circle cx="130" cy="312" r="11"/><path d="M130 306 V312 L135 316"/>
      <path d="M118 480 H142 M118 488 H142 M118 496 H134"/>
      <path d="M1018 136 H1042 M1030 124 V148"/>
      <rect x="1019" y="302" width="22" height="18" rx="2"/><path d="M1024 302 V297 H1036 V302"/>
      <path d="M1018 500 L1026 486 L1034 494 L1042 476"/>
    </g>
  </svg>
  <header class="slide-header">
    <svg width="800" height="56" viewBox="0 0 800 56">
      <path d="M0 0 H690 L656 56 H0 Z" fill="var(--brand-blue)"/>
      <path d="M52 0 H70 L36 56 H18 Z M78 0 H88 L54 56 H44 Z" fill="var(--brand-blue-light)"/>
      <path d="M702 0 H716 L682 56 H668 Z M728 0 H742 L708 56 H694 Z M754 0 H768 L734 56 H720 Z" fill="var(--brand-blue)"/>
    </svg>
    <h2 class="slide-header__title">AEROSPACE ENGINEERING</h2>
    <div class="brand"><span class="brand__mark"></span>Stratavolt</div>
  </header>

  <h3 class="feature-title" style="left:180px;top:112px">NEMO ENIM IPSAM</h3>
  <p class="feature-text" style="left:180px;top:144px">Sed ut perspiciatis unde omnis iste natus error sit voluptatem accusantium doloremque laudantium, totam rem aperiam, eaque ipsa quae ab illo inventore veritatis.</p>
  <h3 class="feature-title" style="left:180px;top:288px">NEMO ENIM IPSAM</h3>
  <p class="feature-text" style="left:180px;top:320px">Sed ut perspiciatis unde omnis iste natus error sit voluptatem accusantium doloremque laudantium, totam rem aperiam, eaque ipsa quae ab illo inventore veritatis.</p>
  <h3 class="feature-title" style="left:180px;top:464px">NEMO ENIM IPSAM</h3>
  <p class="feature-text" style="left:180px;top:496px">Sed ut perspiciatis unde omnis iste natus error sit voluptatem accusantium doloremque laudantium, totam rem aperiam, eaque ipsa quae ab illo inventore veritatis.</p>

  <h3 class="feature-title" style="left:740px;top:112px">NEMO ENIM IPSAM</h3>
  <p class="feature-text" style="left:740px;top:144px">Sed ut perspiciatis unde omnis iste natus error sit voluptatem accusantium doloremque laudantium, totam rem aperiam, eaque ipsa quae ab illo inventore veritatis.</p>
  <h3 class="feature-title" style="left:740px;top:288px">NEMO ENIM IPSAM</h3>
  <p class="feature-text" style="left:740px;top:320px">Sed ut perspiciatis unde omnis iste natus error sit voluptatem accusantium doloremque laudantium, totam rem aperiam, eaque ipsa quae ab illo inventore veritatis.</p>
  <h3 class="feature-title" style="left:740px;top:464px">NEMO ENIM IPSAM</h3>
  <p class="feature-text" style="left:740px;top:496px">Sed ut perspiciatis unde omnis iste natus error sit voluptatem accusantium doloremque laudantium, totam rem aperiam, eaque ipsa quae ab illo inventore veritatis.</p>

  <footer class="slide-footer">
    <svg class="slide-footer__stripes" width="140" height="44" viewBox="0 0 140 44"><path d="M40 0 H58 L30 44 H12 Z M66 0 H76 L48 44 H38 Z" fill="var(--brand-blue-light)"/></svg>
    <p class="copyright">© Copyright 2023 Stratavolt Aero. All rights reserved.</p>
  </footer>
</section>

<!-- Closing -->
<section class="slide slide--thanks thanks">
  <div class="photo thanks__photo" role="img" aria-label="Two engineers in overalls beside a large jet engine"></div>
  <div class="brand"><span class="brand__mark"></span>Stratavolt</div>
  <h1 class="thanks__title">THANK YOU</h1>
  <p class="thanks__tagline">Lorem ipsum dolor sit amet, consectetur adipiscing</p>
  <p class="contact contact--email">
    <svg width="26" height="20" viewBox="0 0 26 20"><rect x="1.5" y="1.5" width="23" height="17" rx="2" fill="none" stroke="var(--ink)" stroke-width="2.4"/><path d="M2 3 L13 11 L24 3" fill="none" stroke="var(--ink)" stroke-width="2.4"/></svg>
    info@stratavolt-aero.com</p>
  <p class="contact contact--phone">
    <svg width="24" height="24" viewBox="0 0 24 24"><path d="M6 2 L10 7 L7.5 9.5 C9 13 11 15 14.5 16.5 L17 14 L22 18 L19 22 C10 21 3 14 2 5 Z" fill="var(--ink)"/></svg>
    +1 555-010-0199</p>
  <div class="socials" aria-label="Social media links"><span></span><span></span><span></span></div>
  <p class="thanks__copy">© Copyright 2023 Stratavolt Aero. All rights reserved.</p>
</section>

</body>
</html>
```